Collectibles expert needs a new business card design.

My current business card makes me look to high end. It may even make me look arrogant or too stuffy. I do work with high end clients and their items but most of my business is with average people with average items. My business name is Walter Brennick's Old Orchard Salvage Co. The idea was that I mine the streets helping people discover the treasures buried in their homes. That could be art, jewelry, coins, etc. The name and an older logo I used does not make immediate sense to most people. I tried to go with just my picture and name and that is the current card I am changing. I help people who need to downsize. Whether they are getting rid of one item, a collection or a house full of items I help them discover what they have, what it is worth and what are the best ways we can get the most for them. This may be a combination of estate sale (which I dont do) auction or sell directly to a dealer or collector. Usually it is a combination of these. My main goal is to help make sure they dont accidently sell a Picasso painting in a garage sale. I am uploading a copy of my old card and the old logo I used to use but the winning card design will need to be much different than these. You can learn a little more about me at www.walterjbrennick.example, www.oldorchardsalv.example and www.facebook.com/oosalco. I hope someone can look at what I do and come up with a very unique design that will be equally effective if my client is high income or if my client is low to mid income. I do not care if it is a one or two sided card as long as it conveys my contact information and a good representation of what I do.

Target Market(s)

People who are getting rid of items. These can be elderly couples or individuals that are moving to an active living community and will have less space so they need to sell items. This can also include the children of elder parents that dont want their stuff and want to find solutions to help them get rid of their items.

Contact Information for Business Card

The card should have my business name Walter Brennick's Old Orchard Salvage Co., phone number 555-302-71938, email walter@oldorchardsalvage.example and website www.oldorchardsalvage.example. Would also like to include Buyer, Broker, Consultant and Appraiser. We can put Walter J. Brennick, ISA on the opposite side of the company name since it includes my name as well.

Font styles to use
Sans Serif

Colors

Designer to choose colors to be used in the design.

Requirements
Must have
• My project must have a professional look. It must not alienate low income clients and should still be appealing to high value clients.

```html
<!DOCTYPE html>
<html lang="en">
<head>
<meta charset="utf-8">
<title>Old Orchard Salvage Co. — Business Card</title>
<link href="https://fonts.googleapis.com/css2?family=Oswald:wght@500;600&family=Lato:wght@400&display=swap" rel="stylesheet">
<style>
  :root {
    --backdrop: #4a4a4a;
    --card-light: #f7f7f7;
    --card-dark: #352d23;
    --gold: #9a6b23;
    --gold-bright: #a8782e;
    --slate: #5a5a5a;
    --ink: #3a3a3a;
    --rule: #b5b5b5;
    --white: #ffffff;
  }
  * { margin: 0; padding: 0; box-sizing: border-box; }
  html, body {
    width: 1200px; height: 802px; overflow: hidden;
    background: var(--backdrop);
  }
  .canvas { position: relative; width: 1200px; height: 802px; }
  .card {
    position: absolute; top: 274px;
    width: 442px; height: 264px;
    box-shadow: 0 3px 8px rgba(0,0,0,.45);
  }
  .card--front { left: 136px; background: var(--card-light); }
  .card--back { left: 624px; background: var(--card-dark); }

  .front__brand {
    position: absolute; left: 36px; top: 82px;
    width: 118px; height: 101px;
    display: flex; flex-direction: column; justify-content: center; align-items: center;
    gap: 8px; text-align: center;
  }
  .front__brand-mark { width: 14px; height: 14px; background: var(--gold); }
  .front__brand-name {
    font-family: 'Oswald', sans-serif; font-weight: 500;
    font-size: 17px; line-height: 1.15; text-transform: uppercase;
    color: var(--slate); letter-spacing: .3px;
  }
  .front__divider {
    position: absolute; left: 170px; top: 89px;
    width: 1px; height: 88px; background: var(--rule);
  }
  .front__details { position: absolute; left: 185px; top: 84px; }
  .holder-name {
    font-family: 'Oswald', sans-serif; font-weight: 500;
    font-size: 17px; line-height: 22px; color: var(--gold);
    text-transform: uppercase; letter-spacing: -.2px;
  }
  .holder-role {
    font-family: 'Lato', sans-serif; font-size: 13px; color: var(--ink);
    line-height: 16px;
  }
  .contact-list { list-style: none; margin-top: 13px; }
  .contact-list li {
    display: flex; align-items: center; gap: 5px;
    font-family: 'Lato', sans-serif; font-size: 12.5px; line-height: 16px; color: var(--ink);
  }
  .contact-list svg { width: 10px; height: 10px; flex: none; fill: var(--gold-bright); }

  .back__brand {
    position: absolute; left: 0; right: 0; top: 70px;
    display: flex; flex-direction: column; align-items: center; gap: 18px;
    text-align: center;
  }
  .back__brand-mark { width: 58px; height: 58px; border-radius: 50%; background: var(--gold-bright); }
  .back__brand-name {
    font-family: 'Oswald', sans-serif; font-weight: 600;
    font-size: 21px; line-height: 1.2; color: var(--white);
    text-transform: uppercase;
  }
</style>
</head>
<body>
<main class="canvas">
  <section class="card card--front" aria-label="Business card front">
    <div class="front__brand">
      <span class="front__brand-mark"></span>
      <span class="front__brand-name">Old Orchard<br>Salvage Co.</span>
    </div>
    <div class="front__divider"></div>
    <div class="front__details">
      <h1 class="holder-name">Walter J. Brennick, ISA</h1>
      <p class="holder-role">Buyer, Broker, Consultant and Appraiser</p>
      <ul class="contact-list">
        <li>
          <svg viewBox="0 0 10 10" aria-hidden="true"><path d="M1 3.5C1 2 2.5 1.5 5 1.5S9 2 9 3.5L7.5 4 7 3H3L2.5 4ZM2.5 5h5l1 3.5h-7Z"/></svg>
          555-302-71938
        </li>
        <li>
          <svg viewBox="0 0 10 10" aria-hidden="true"><path d="M0.5 2h9v6h-9Z M1 2.5l4 3 4-3" stroke="#f7f7f7" stroke-width=".7"/></svg>
          walter@oldorchardsalvage.example
        </li>
        <li>
          <svg viewBox="0 0 10 10" aria-hidden="true"><circle cx="5" cy="5" r="4.5"/><path d="M3 3.5l1.5-1 1 1.5-1 1.5 1.5 1-.5 1.5" stroke="#f7f7f7" stroke-width=".8" fill="none"/></svg>
          www.oldorchardsalvage.example
        </li>
      </ul>
    </div>
  </section>

  <section class="card card--back" aria-label="Business card back">
    <div class="back__brand">
      <span class="back__brand-mark"></span>
      <p class="back__brand-name">Walter Brennick's<br>Old Orchard Salvage Co.</p>
    </div>
  </section>
</main>
</body>
</html>
```